BLPR Postcard Design: Mosquito Control, Lawn Maintenance and Pressure washing

I have a new company based in Atlanta,Georgia named Birchfield Lawn Pest Relief, LLC. We specializes in Mosquito Control. We also have additional services: Lawn maintenance, Pressure Washing and Gutter Cleaning. I would like to see designs with the colors Black, Red, Gray. We would like the customer to think of us when it comes to Enjoying a mosquito free yard and improving the look and feel of their home and lawn.

Industry/Entity Type

It Company

Requirements
Nice to have
• Treatment plans starting at $69/mt - front of card
• The additional services we offer - back of card.

```html
<!DOCTYPE html>
<html lang="en">
<head>
<meta charset="utf-8">
<title>Birchfield Lawn Pest Relief, LLC – Postcard</title>
<link rel="stylesheet" href="https://fonts.googleapis.com/css2?family=Titan+One&family=Saira+Condensed:wght@700&family=Russo+One&family=Exo+2:ital,wght@1,900&display=swap">
<style>
  :root {
    --red: #d7191f;
    --red-deep: #8e0f14;
    --black: #151515;
    --charcoal: #262626;
    --gray-panel: #dcdcdc;
    --gray-light: #ececec;
    --white: #ffffff;
    --ink: #1c1c1c;
    --page: #e6e6e6;
  }
  * { box-sizing: border-box; margin: 0; padding: 0; }
  html, body { width: 1200px; height: 1000px; overflow: hidden; }
  body { background: var(--page); position: relative; font-family: "Saira Condensed", sans-serif; }

  .postcard { position: absolute; width: 760px; height: 470px; box-shadow: 0 6px 18px rgba(0,0,0,.25); overflow: hidden; }

  /* Front */
  .postcard--front { left: 410px; top: 28px; background: linear-gradient(160deg, var(--charcoal), var(--black)); }
  .brand { text-align: center; }
  .brand__name { font-family: "Titan One", sans-serif; color: var(--red); line-height: 1; text-shadow: 2px 3px 0 rgba(0,0,0,.45); }
  .brand__tagline { font-family: "Saira Condensed", sans-serif; font-weight: 700; line-height: 1.05; letter-spacing: .5px; }
  .brand__phone { font-family: "Russo One", sans-serif; color: var(--red); line-height: 1.1; letter-spacing: 1px; }

  .postcard--front .brand { position: absolute; left: 0; right: 0; top: 22px; }
  .postcard--front .brand__name { font-size: 80px; }
  .postcard--front .brand__tagline { color: var(--white); font-size: 38px; margin-top: 4px; text-shadow: 2px 2px 0 #000; }
  .postcard--front .brand__phone { font-size: 58px; margin-top: 2px; }

  .offer-band { position: absolute; left: 0; right: 0; top: 262px; height: 150px; background: linear-gradient(180deg, var(--red), var(--red-deep)); }
  .offer { position: absolute; left: 40px; top: 14px; font-family: "Exo 2", sans-serif; font-style: italic; font-weight: 900; color: var(--white); text-shadow: 2px 3px 0 rgba(0,0,0,.55); line-height: 1.05; }
  .offer__lead { font-size: 36px; display: block; }
  .offer__price { font-size: 60px; display: block; margin-top: 2px; }

  .no-mosquito { position: absolute; left: 470px; top: 198px; width: 272px; height: 272px; }

  /* Back */
  .postcard--back { left: 30px; top: 512px; background: var(--white); }
  .services-panel { position: absolute; left: 0; top: 0; width: 500px; height: 402px; background: linear-gradient(180deg, var(--gray-light), var(--gray-panel)); }
  .postcard--back .brand { position: absolute; left: 0; right: 0; top: 14px; }
  .postcard--back .brand__name { font-size: 52px; }
  .postcard--back .brand__tagline { color: var(--ink); font-size: 28px; margin-top: 2px; }
  .postcard--back .brand__phone { font-size: 40px; margin-top: 2px; }

  .photo { position: absolute; border: 3px solid var(--white); box-shadow: 0 2px 5px rgba(0,0,0,.35); }
  .photo--mowing { left: 40px; top: 190px; width: 160px; height: 106px; background: linear-gradient(180deg, #6f8f52 0%, #4f7a34 60%, #3b6b2a 100%); }
  .photo--washing { left: 40px; top: 304px; width: 160px; height: 88px; background: linear-gradient(180deg, #6d7467, #9a9e98); }
  .photo--gutters { left: 208px; top: 300px; width: 152px; height: 92px; background: linear-gradient(180deg, #4a5a6e, #7a6a40); }

  .service-list { position: absolute; left: 212px; top: 186px; list-style: none; font-family: "Exo 2", sans-serif; font-style: italic; font-weight: 900; font-size: 22px; color: var(--ink); line-height: 1.2; }
  .service-list li::before { content: ""; display: inline-block; width: 7px; height: 7px; border-radius: 50%; background: var(--red); margin-right: 7px; vertical-align: middle; }
</style>
</head>
<body>

<section class="postcard postcard--front" aria-label="Postcard front">
  <header class="brand">
    <h1 class="brand__name">Birchfield</h1>
    <p class="brand__tagline">Lawn Pest Relief, LLC</p>
    <p class="brand__phone">404-555-0187</p>
  </header>
  <div class="offer-band">
    <p class="offer">
      <span class="offer__lead">Treatment plans</span>
      <span class="offer__lead">starting at</span>
      <span class="offer__price">$69/mt</span>
    </p>
  </div>
  <svg class="no-mosquito" viewBox="0 0 272 272" aria-label="No mosquitoes sign">
    <defs>
      <radialGradient id="bite-skin" cx="50%" cy="45%" r="60%">
        <stop offset="0" stop-color="#d6d6d6"/>
        <stop offset="1" stop-color="#9d9d9d"/>
      </radialGradient>
      <path id="ring-arc" d="M 36 190 A 108 108 0 0 1 200 44"/>
    </defs>
    <circle cx="136" cy="136" r="132" fill="var(--white)"/>
    <circle cx="136" cy="136" r="104" fill="url(#bite-skin)" role="img" aria-label="Photo of a mosquito on skin"/>
    <circle cx="136" cy="136" r="117" fill="none" stroke="var(--red)" stroke-width="26"/>
    <line x1="62" y1="62" x2="210" y2="210" stroke="var(--red)" stroke-width="24"/>
    <text font-family="'Exo 2', sans-serif" font-style="italic" font-weight="900" font-size="17" fill="#fff">
      <textPath href="#ring-arc" startOffset="6">Enjoy a mosquito free yard!</textPath>
    </text>
  </svg>
</section>

<section class="postcard postcard--back" aria-label="Postcard back">
  <div class="services-panel">
    <header class="brand">
      <h2 class="brand__name">Birchfield</h2>
      <p class="brand__tagline">Lawn Pest Relief, LLC</p>
      <p class="brand__phone">404-555-0187</p>
    </header>
    <div class="photo photo--mowing" role="img" aria-label="Photo of a red lawn mower on grass"></div>
    <ul class="service-list">
      <li>Mosquito Control</li>
      <li>Lawn Maintenance</li>
      <li>Pressure Washing</li>
      <li>Gutter Cleaning</li>
    </ul>
    <div class="photo photo--washing" role="img" aria-label="Photo of pressure washing a driveway"></div>
    <div class="photo photo--gutters" role="img" aria-label="Photo of gutter cleaning with leaves"></div>
  </div>
</section>

</body>
</html>
```